Business card design for my company.
I would like the card's background colour to be black. You can also see our web site to get an idea of our brand. https://www.tmwhomecrafting.com.au/
- Name
- Email

```html
<!DOCTYPE html>
<html lang="en">
<head>
<meta charset="utf-8">
<title>TMW Home Crafting – Business Card</title>
<link rel="stylesheet" href="https://fonts.googleapis.com/css2?family=Montserrat:wght@500;700&display=swap">
<style>
  :root {
    --page-bg: #d3cec7;
    --card-dark: #1f1f1f;
    --card-light: #ebe6de;
    --brand-green: #1f8a3f;
    --line-dark: #111111;
    --logo-grey: #cbc7c0;
    --text-dark: #1c1c1c;
  }
  * { margin: 0; padding: 0; box-sizing: border-box; }
  html, body {
    width: 1200px;
    height: 1047px;
    overflow: hidden;
    background: var(--page-bg);
    font-family: "Montserrat", Arial, sans-serif;
  }
  .business-card {
    position: absolute;
    left: 100px;
    top: 237px;
    width: 1000px;
    height: 572px;
    border-radius: 24px;
    overflow: hidden;
    background: var(--card-light);
    box-shadow: 0 12px 40px rgba(0,0,0,0.18);
  }
  .card-art { position: absolute; inset: 0; width: 100%; height: 100%; }
  .brand-name {
    position: absolute;
    left: 52px;
    top: 118px;
    color: var(--logo-grey);
    font-weight: 700;
    line-height: 1;
  }
  .brand-name .brand-main { display: block; font-size: 120px; letter-spacing: 4px; }
  .brand-name .brand-sub { display: block; font-size: 31px; letter-spacing: 6px; margin-top: 14px; }
  .contact-block {
    position: absolute;
    right: 36px;
    top: 232px;
    text-align: right;
    color: var(--text-dark);
    font-weight: 500;
  }
  .person-name {
    color: var(--brand-green);
    font-size: 39px;
    font-weight: 700;
    letter-spacing: 0.5px;
  }
  .person-title { font-size: 23px; margin-top: 6px; margin-right: 2px; }
  .location { font-size: 23px; margin-top: 36px; }
  .contact-list { list-style: none; margin-top: 30px; }
  .contact-list li {
    display: flex;
    justify-content: flex-end;
    align-items: center;
    gap: 6px;
    font-size: 23px;
    line-height: 1.72;
  }
  .contact-icon { width: 20px; height: 20px; flex: none; }
</style>
</head>
<body>
  <section class="business-card">
    <svg class="card-art" viewBox="0 0 1000 572" aria-hidden="true">
      <path class="dark-panel" d="M0 0 H1000 V176 C820 154 660 229 530 314 C410 396 300 476 190 476 C110 476 40 446 0 426 Z" fill="var(--card-dark)"/>
      <path class="swoosh-green" d="M1000 172 C820 150 660 225 530 310 C410 392 300 472 190 472 C110 472 40 442 0 422" fill="none" stroke="var(--brand-green)" stroke-width="9"/>
      <path class="swoosh-dark" d="M1000 186 C820 164 660 239 530 324 C410 406 300 486 190 486 C110 486 40 456 0 436" fill="none" stroke="var(--line-dark)" stroke-width="6"/>
    </svg>

    <div class="brand-name">
      <span class="brand-main">TMW</span>
      <span class="brand-sub">HOME CRAFTING</span>
    </div>

    <div class="contact-block">
      <h1 class="person-name">Liam Hartley</h1>
      <p class="person-title">General Manager</p>
      <p class="location">Riverton, Tasmania, Australia</p>
      <ul class="contact-list">
        <li>0400 555 018
          <svg class="contact-icon" viewBox="0 0 20 20"><path d="M3 8 C3 5 6 4 10 4 C14 4 17 5 17 8 L14 9 L13 7 L7 7 L6 9 Z M5 11 H15 L16 16 H4 Z" fill="var(--brand-green)"/></svg>
        </li>
        <li>info@tmwhomecrafting.com.au
          <svg class="contact-icon" viewBox="0 0 20 20"><rect x="2" y="5" width="16" height="11" fill="var(--brand-green)"/><path d="M2 5 L10 11 L18 5" fill="none" stroke="#ffffff" stroke-width="1.4"/></svg>
        </li>
        <li>www.tmwhomecrafting.com.au
          <svg class="contact-icon" viewBox="0 0 20 20"><circle cx="10" cy="10" r="8" fill="var(--brand-green)"/><path d="M6 6 C8 7 9 9 8 11 C7 13 9 14 10 16 M12 4 C12 7 15 8 17 9" fill="none" stroke="#ffffff" stroke-width="1.4"/></svg>
        </li>
      </ul>
    </div>
  </section>
</body>
</html>
```